Coastal Learner Bureau business cards

Australian company about to start offering its services. We recruit international students to come to study English, vocational education and postgraduate courses in Australia. We help them find the institution and select the right city they want to come to Australia. We are a young, online oriented and supportive agency. Our clients are between 18 and 35 years old, mainly University students, young professionals or people with work experience. We provide much more information that any other agency offer. We administrate a Facebook group with more than 11.000 members that daily ask questions about general information when coming to Australia, while they are here and even after they leave the country

Target Market(s)

International students from South America, Central America and Europe

Industry/Entity Type

Student

Contact Information for Business Card

Tomas Bilbrea
Managing Director
tomas@kelvarin.com.au
www.kelvoria.com.au
+61 491058264
Melbourne, Australia

Font styles to use
Serif
Sans Serif

Colors

Designer to choose colors to be used in the design.

Requirements
Must have
• Horizontal design
• Standard business card size and shape. If font uses green or yellow colours, they will have to match the ones from the logo
Nice to have
• UPDATE: Use the contents of the green image to design one of the card sides. Use our logo in the background of that side as watermark.
• Passport image, or immigration stamps. A picture of the Yarra River (from Melbourne) would be cool as well.
Should not have
• Non-standard business card size and shape
• Not black as the background colour of any sides as we are not a VIP agency or a hight class service. We are orientes to young people and they like colours, pictures, something attractive.
• Vertical design
• NO YELLOW or BLACK AS THE BACKGROUND COLOUR OF ANY SIDE OF THE BIZ CARD

```html
<!DOCTYPE html>
<html lang="en">
<head>
<meta charset="utf-8">
<title>Coastal Learner Bureau business cards</title>
<link href="https://fonts.googleapis.com/css2?family=Roboto:wght@400;500;700&family=Roboto+Condensed:wght@700&display=swap" rel="stylesheet">
<style>
  :root {
    --stage: #2a2a2a;
    --green: #105e3d;
    --gold: #dfb50f;
    --paper: #f3f3f2;
    --ink: #454545;
    --white: #ffffff;
  }
  * { margin: 0; padding: 0; box-sizing: border-box; }
  html, body { width: 1200px; height: 960px; overflow: hidden; }
  body {
    background: var(--stage);
    font-family: "Roboto", Arial, sans-serif;
    position: relative;
  }
  .card {
    position: absolute;
    width: 600px;
    height: 343px;
    overflow: hidden;
  }
  .card-front { left: 314px; top: 113px; background: var(--paper); }
  .card-back { left: 311px; top: 472px; background: var(--green); }

  .wave { position: absolute; inset: 0; }

  .holder { position: absolute; left: 38px; top: 33px; }
  .holder-name {
    font-family: "Roboto Condensed", "Arial Narrow", sans-serif;
    font-weight: 700;
    font-size: 21px;
    line-height: 24px;
    color: var(--gold);
    letter-spacing: 0.2px;
  }
  .holder-role {
    font-weight: 500;
    font-size: 15px;
    line-height: 18px;
    color: var(--white);
  }

  .brand {
    position: absolute;
    display: flex;
    align-items: center;
    gap: 10px;
    font-family: "Roboto", Arial, sans-serif;
    font-weight: 700;
  }
  .brand-mark { border-radius: 50%; flex: none; }
  .brand-front { right: 40px; top: 92px; color: var(--green); font-size: 40px; }
  .brand-front .brand-mark { width: 18px; height: 18px; background: var(--green); }
  .brand-back {
    left: 0; right: 0; top: 132px;
    justify-content: center;
    color: var(--white);
    font-size: 64px;
  }
  .brand-back .brand-mark { width: 26px; height: 26px; background: var(--gold); }

  .contact {
    position: absolute;
    right: 40px;
    top: 226px;
    list-style: none;
    text-align: right;
    font-size: 14.5px;
    color: var(--ink);
    line-height: 19.5px;
  }
  .contact li { display: flex; justify-content: flex-end; align-items: center; gap: 6px; }
  .contact .city { margin-bottom: 4px; }
  .contact svg { width: 13px; height: 13px; fill: var(--green); flex: none; }

  .tagline {
    position: absolute;
    left: 80px; right: 80px; top: 299px;
    display: flex; align-items: center; gap: 4px;
    color: var(--white);
    font-size: 14px;
  }
  .tagline::before, .tagline::after {
    content: "";
    flex: 1;
    height: 1px;
  }
  .tagline::before { background: linear-gradient(to right, transparent, var(--gold)); }
  .tagline::after { background: linear-gradient(to left, transparent, var(--gold)); }
</style>
</head>
<body>
  <section class="card card-front" aria-label="Business card front">
    <svg class="wave" viewBox="0 0 600 343" width="600" height="343" aria-hidden="true">
      <path d="M0,0 H428 C350,14 318,62 282,140 C244,222 176,296 0,318 Z" fill="var(--gold)"/>
      <path d="M0,0 H416 C336,16 300,62 262,146 C226,226 156,292 0,310 Z" fill="var(--green)" stroke="var(--white)" stroke-width="1.5"/>
    </svg>

    <div class="holder">
      <p class="holder-name">TOMAS BILBREA</p>
      <p class="holder-role">Managing Director</p>
    </div>

    <div class="brand brand-front">
      <span class="brand-mark"></span>
      <span class="brand-name">Kelvoria</span>
    </div>

    <ul class="contact">
      <li class="city">Melbourne, Australia</li>
      <li>+61 491058264
        <svg viewBox="0 0 24 24"><path d="M6.6 10.8a15.1 15.1 0 0 0 6.6 6.6l2.2-2.2a1 1 0 0 1 1-.25 11.4 11.4 0 0 0 3.6.57 1 1 0 0 1 1 1V20a1 1 0 0 1-1 1A17 17 0 0 1 3 4a1 1 0 0 1 1-1h3.5a1 1 0 0 1 1 1c0 1.25.2 2.45.57 3.57a1 1 0 0 1-.25 1z"/></svg>
      </li>
      <li>tomas@kelvarin.com.au
        <svg viewBox="0 0 24 24"><path d="M2 5h20v14H2z M2 5l10 8 10-8" fill="var(--green)" stroke="var(--paper)" stroke-width="1.6"/></svg>
      </li>
      <li>www.kelvoria.com.au
        <svg viewBox="0 0 24 24"><circle cx="12" cy="12" r="11"/><path d="M5 8c3 1 4 4 3 7M14 4c-1 3 2 4 4 5M13 20c1-3 4-3 5-5" fill="none" stroke="var(--paper)" stroke-width="2"/></svg>
      </li>
    </ul>
  </section>

  <section class="card card-back" aria-label="Business card back">
    <div class="brand brand-back">
      <span class="brand-mark"></span>
      <span class="brand-name">Kelvoria</span>
    </div>
    <p class="tagline">Hacemos más por ti!</p>
  </section>
</body>
</html>
```